Investment Advisor E-Newsletter Banner Design

I need a banner designed for an email newsletter that will be sent monthly to clients and prospects. We want to see designs that are elegant and use our logo well. The banner should be 922x150px and should go well with the www.tlvbanda.com website. Should include Logo and email and phone number.

Target Market(s)

High net worth investors

Number of Pages Required

1 page

Requirements
Must have
• logo, place for email (info@tlvbanda.com) and phone number (415-297-6180), colors and design that work well with www.tlvbanda.com website

```html
<!DOCTYPE html>
<html lang="en">
<head>
<meta charset="utf-8">
<title>E-Newsletter Banner</title>
<link rel="stylesheet" href="https://fonts.googleapis.com/css2?family=Montserrat:wght@500&display=swap">
<style>
  :root {
    --page-bg: #ececec;
    --banner-white: #ffffff;
    --banner-purple: #30258f;
    --icon-circle: #1e1867;
    --divider: rgba(255, 255, 255, 0.35);
    --text-light: #ffffff;
    --brand-ink: #1d12b0;
  }
  html, body {
    margin: 0;
    padding: 0;
    width: 1200px;
    height: 1200px;
    overflow: hidden;
    background: var(--page-bg);
  }
  .canvas {
    position: relative;
    width: 1200px;
    height: 1200px;
  }
  .banner {
    position: absolute;
    left: 47px;
    top: 510px;
    width: 1106px;
    height: 180px;
    font-family: "Montserrat", Arial, sans-serif;
  }
  .banner-shape {
    position: absolute;
    inset: 0;
  }
  .brand {
    position: absolute;
    left: 30px;
    top: 0;
    height: 180px;
    display: flex;
    align-items: center;
    gap: 14px;
  }
  .brand-dot {
    width: 30px;
    height: 30px;
    border-radius: 50%;
    background: var(--brand-ink);
  }
  .brand-name {
    color: var(--brand-ink);
    font-size: 31px;
    font-weight: 500;
    letter-spacing: 0.2px;
  }
  .title {
    position: absolute;
    left: 455px;
    top: 0;
    height: 180px;
    display: flex;
    align-items: center;
    color: var(--text-light);
    font-size: 31px;
    font-weight: 500;
    letter-spacing: 0.5px;
  }
  .divider {
    position: absolute;
    left: 736px;
    top: 53px;
    width: 1px;
    height: 76px;
    background: var(--divider);
  }
  .contacts {
    position: absolute;
    left: 770px;
    top: 51px;
    display: flex;
    flex-direction: column;
    gap: 11px;
  }
  .contact-row {
    display: flex;
    align-items: center;
    gap: 11px;
    color: var(--text-light);
    font-size: 26px;
    font-weight: 500;
    line-height: 32px;
  }
  .contact-icon {
    width: 32px;
    height: 32px;
    border-radius: 50%;
    background: var(--icon-circle);
    display: flex;
    align-items: center;
    justify-content: center;
  }
</style>
</head>
<body>
<div class="canvas">
  <div class="banner">
    <svg class="banner-shape" width="1106" height="180" viewBox="0 0 1106 180">
      <rect x="0" y="0" width="1106" height="180" fill="var(--banner-white)"/>
      <polygon points="431,0 1106,0 1106,180 322,180" fill="var(--banner-purple)"/>
    </svg>

    <div class="brand">
      <span class="brand-dot"></span>
      <span class="brand-name">Tidevale Capital</span>
    </div>

    <div class="title">E-NEWSLETTER</div>

    <div class="divider"></div>

    <div class="contacts">
      <div class="contact-row">
        <span class="contact-icon">
          <svg width="14" height="14" viewBox="0 0 24 24"><path fill="#ffffff" d="M6.6 10.8c1.4 2.8 3.8 5.1 6.6 6.6l2.2-2.2c.3-.3.7-.4 1-.2 1.1.4 2.3.6 3.6.6.6 0 1 .4 1 1V20c0 .6-.4 1-1 1C10.6 21 3 13.4 3 4c0-.6.4-1 1-1h3.5c.6 0 1 .4 1 1 0 1.3.2 2.5.6 3.6.1.3 0 .7-.2 1z"/></svg>
        </span>
        <span class="contact-text">415-297-6180</span>
      </div>
      <div class="contact-row">
        <span class="contact-icon">
          <svg width="14" height="14" viewBox="0 0 24 24"><path fill="#ffffff" d="M3 5h18c.6 0 1 .4 1 1v.6l-10 6.2L2 6.6V6c0-.6.4-1 1-1zm-1 3.9l10 6.2 10-6.2V18c0 .6-.4 1-1 1H3c-.6 0-1-.4-1-1z"/></svg>
        </span>
        <span class="contact-text">info@tlvbanda.com</span>
      </div>
    </div>
  </div>
</div>
</body>
</html>
```